Bluecrest Learning Corps by graduating students from college in two years

Based on the logo design, create stationary and business cards for
Dr. Venrel T Oskamp, CEO, (703) 482-1736
and Marisa Deltoft, Respresentative, (301) 647-2208
Address: 4719 Pellham Court, Harlow Ridge, VA 22817
Incorporate elelments of the logo

Target Market(s)

USA

Font styles to use
Other font styles liked:
• match with the logo type style

```html
<!DOCTYPE html>
<html lang="en">
<head>
<meta charset="utf-8">
<title>Bluecrest Learning Corps Letterhead</title>
<link href="https://fonts.googleapis.com/css2?family=Arimo:wght@400;700&family=Mulish:wght@700&display=swap" rel="stylesheet">
<style>
  :root {
    --backdrop: #e2e2e2;
    --paper: #ffffff;
    --navy: #17256a;
    --gold: #f6c432;
    --body-grey: #555555;
    --heading-grey: #4a4a4a;
    --signature-tone: #d4d4d4;
  }
  html, body {
    margin: 0;
    width: 1153px;
    height: 1200px;
    overflow: hidden;
    background: var(--backdrop);
  }
  .letterhead {
    position: absolute;
    left: 222px;
    top: 128px;
    width: 671px;
    height: 950px;
    background: var(--paper);
    font-family: "Arimo", Arial, sans-serif;
  }
  .brand {
    position: absolute;
    left: 48px;
    top: 84px;
    display: flex;
    align-items: center;
    gap: 10px;
  }
  .brand-dot {
    width: 30px;
    height: 30px;
    border-radius: 50%;
    background: var(--gold);
  }
  .brand-name {
    font-family: "Arimo", Arial, sans-serif;
    font-weight: 700;
    font-size: 15px;
    color: var(--navy);
  }
  .salutation {
    position: absolute;
    left: 61px;
    top: 292px;
    margin: 0;
    font-family: "Mulish", "Century Gothic", sans-serif;
    font-weight: 700;
    font-size: 16px;
    color: var(--heading-grey);
  }
  .letter-body {
    position: absolute;
    left: 60px;
    top: 336px;
    width: 570px;
    font-size: 11.7px;
    line-height: 13.8px;
    color: var(--body-grey);
  }
  .letter-body p { margin: 0 0 12.4px; }
  .letter-body .line { display: block; white-space: nowrap; }
  .closing {
    position: absolute;
    left: 61px;
    top: 621px;
    margin: 0;
    font-family: "Mulish", "Century Gothic", sans-serif;
    font-weight: 700;
    font-size: 9px;
    color: var(--heading-grey);
  }
  .signature {
    position: absolute;
    left: 56px;
    top: 664px;
    width: 84px;
    height: 25px;
    background: linear-gradient(90deg, var(--signature-tone), #e6e6e6);
    border-radius: 3px;
  }
  .footer-contact {
    position: absolute;
    top: 860px;
    font-size: 11.3px;
    line-height: 13.6px;
    color: var(--body-grey);
  }
  .footer-contact .name {
    font-weight: 700;
    font-size: 13.5px;
    line-height: 15px;
    color: var(--navy);
  }
  .footer-contact .phone { margin-top: 3px; display: flex; align-items: center; gap: 3px; }
  .footer-contact.is-left { left: 43px; }
  .footer-contact.is-right { right: 43px; text-align: right; }
  .footer-contact.is-right .phone { justify-content: flex-end; }
  .footer-address {
    position: absolute;
    left: 0;
    width: 671px;
    top: 863px;
    text-align: center;
    font-size: 11.3px;
    line-height: 13.6px;
    color: var(--body-grey);
  }
  .footer-rule {
    position: absolute;
    left: 43px;
    top: 911px;
    width: 585px;
    height: 3px;
    background: var(--gold);
  }
  .phone-icon { width: 10px; height: 9px; fill: var(--gold); }
</style>
</head>
<body>
<main class="letterhead">
  <div class="brand">
    <span class="brand-dot"></span>
    <span class="brand-name">Bluecrest Learning Corps</span>
  </div>

  <h1 class="salutation">Dear Mr. Halvorsen,</h1>

  <div class="letter-body">
    <p>
      <span class="line">Lorem ipsum dolor sit amet, consectetuer adipiscing elit, sed diam nonmmy nibh euismod tincidunt ut laor</span>
      <span class="line">eet dolore magna aliquam erat volutpat. Ut wisi enim ad minim veniam, quis nostrud exerci tationmcorper</span>
      <span class="line">suscipit lobortis nisl ut aliquip ex ea commodo consequat. Duis autem vel eum iriure dolor in hendrerit in</span>
      <span class="line">vulputate velit esse molestie consequat, vel illum dolore eu feugiat</span>
    </p>
    <p>
      <span class="line">Rorem ipsum dolor sit amet, consectetuer adipiscing elit, sed diam nonmmy nibh euismod tincidunt ut laor</span>
      <span class="line">eet dolore magna aliquam erat volutpat. Ut wisi enim ad minim veniam, quis nostrud exerci tationmcorper</span>
      <span class="line">suscipit lobortis nisl ut aliquip ex ea commodo consequat. Duis autem vel eum iriure dolor in hendrerit in</span>
      <span class="line">vulputate velit esse molest</span>
    </p>
    <p>
      <span class="line">Dorem ipsum dolor sit amet, consectetuer adipiscing elit, sed diam nonmmy nibh euismod tincidunt ut laor</span>
      <span class="line">eet dolore magna aliquam erat volutpat. Ut wisi enim ad minim veniam, quis nostrud exerci tationmcorper</span>
      <span class="line">suscipit lobortis nisl ut aliquip ex ea commodo consequat. Duis autem vel eum iriure dolor in hendrerit in</span>
      <span class="line">suscipit lobortis nisl ut aliquip ex ea commodo consequat. Duis autem vel eum iriure dolor in hendrerit in</span>
      <span class="line">vulputate velit esse molestie consequat, vel illum</span>
    </p>
    <p>
      <span class="line">Sorem ipsum dolor sit amet, consectetuer adipiscing elit, sed diam nonmmy nibh euismod tincidunt ut laor</span>
      <span class="line">eet dolore magna aliquam erat volutpat. Ut wisi enim ad minim veniam, quis nostrud exerci tationmcorper</span>
      <span class="line">suscipit lobortis nisl ut aliquip ex ea commodo consequat. Duis autem vel eum iriure dolor in</span>
    </p>
  </div>

  <p class="closing">Sincerely,</p>
  <div class="signature" role="img" aria-label="Handwritten signature of Tobin Argall"></div>

  <div class="footer-contact is-left">
    <div class="name">Dr. Venrel T Oskamp</div>
    <div class="role">CEO</div>
    <div class="phone">
      <svg class="phone-icon" viewBox="0 0 20 18" aria-hidden="true"><path d="M2 6c0-3 4-5 8-5s8 2 8 5l-3 1-1-3H6L5 7z M4 9h12l2 8H2z"/></svg>
      (703) 482-1736
    </div>
  </div>

  <div class="footer-address">
    4719 Pellham Court<br>
    Harlow Ridge<br>
    VA 22817
  </div>

  <div class="footer-contact is-right">
    <div class="name">Marisa Deltoft</div>
    <div class="role">Respresentative</div>
    <div class="phone">
      <svg class="phone-icon" viewBox="0 0 20 18" aria-hidden="true"><path d="M2 6c0-3 4-5 8-5s8 2 8 5l-3 1-1-3H6L5 7z M4 9h12l2 8H2z"/></svg>
      (301) 647-2208
    </div>
  </div>

  <div class="footer-rule"></div>
</main>
</body>
</html>
```